We are a recruitment company based in Norwich/Cambridge England.
I have included our company logo which we want to remain the same.

What we are looking for is a new creative Business card which will really stand out!!

Contact Information for Business Card

Harriet Dunmore
email: Harriet@plavex.co.uk
Address: Brackwell House
Fenmoor Enterprise Park
Partridge Way
Norwich
QB9 3KX
Tel:01632 960418

```html
<!DOCTYPE html>
<html lang="en">
<head>
<meta charset="utf-8">
<title>Plavex Business Card</title>
<link href="https://fonts.googleapis.com/css2?family=Montserrat:wght@500;600&family=Open+Sans:wght@400;700&display=swap" rel="stylesheet">
<style>
  :root {
    --backdrop: #cbcbcb;
    --card-light: #ffffff;
    --card-dark: #2c2c2c;
    --brand-grey: #8d8a8f;
    --brand-green: #8cc63f;
    --ink: #2a2a2a;
    --white: #ffffff;
  }
  * { margin: 0; padding: 0; box-sizing: border-box; }
  html, body { width: 1200px; height: 900px; overflow: hidden; }
  body {
    background: var(--backdrop);
    font-family: "Open Sans", Arial, sans-serif;
    position: relative;
  }
  .card {
    position: absolute;
    top: 306px;
    width: 440px;
    height: 272px;
    border-radius: 10px;
    overflow: hidden;
    box-shadow: 2px 3px 5px rgba(0,0,0,0.35);
  }
  .card--front { left: 149px; background: var(--card-light); }
  .card--back { left: 608px; background: var(--card-dark); }

  .header-band {
    position: absolute; left: 0; top: 0; width: 100%; height: 94px;
    background: var(--brand-grey);
  }
  .header-accent {
    position: absolute; right: 0; top: 0; width: 108px; height: 94px;
    background: var(--brand-green);
  }
  .brand-name {
    font-family: "Montserrat", Arial, sans-serif;
    font-weight: 600;
    line-height: 1;
  }
  .header-band .brand-name {
    position: absolute; left: 23px; top: 32px;
    font-size: 31px; color: var(--white);
  }
  .tagline {
    font-family: "Montserrat", Arial, sans-serif;
    font-weight: 500;
    letter-spacing: 1.3px;
    line-height: 1;
  }
  .header-band .tagline {
    position: absolute; left: 24px; top: 66px;
    font-size: 6px; color: var(--white);
  }

  .holder { position: absolute; left: 24px; top: 143px; }
  .holder-name {
    font-family: "Montserrat", Arial, sans-serif;
    font-weight: 600; font-size: 16px; line-height: 1;
    color: var(--brand-grey);
  }
  .holder-name .first { color: var(--brand-green); }
  .holder-role { font-size: 12px; color: var(--ink); margin-top: 3px; }

  .contacts {
    position: absolute; left: 24px; top: 189px;
    list-style: none; font-size: 12.5px; color: var(--ink);
  }
  .contacts li { display: flex; align-items: center; height: 16px; }
  .contacts svg { width: 9px; height: 9px; margin-right: 4px; fill: var(--brand-green); }

  .address {
    position: absolute; right: 20px; top: 221px;
    font-size: 12.5px; line-height: 16px; color: var(--ink);
    text-align: right; font-style: normal;
  }

  .back-lockup {
    position: absolute; left: 70px; top: 100px;
    display: flex; align-items: center;
  }
  .back-dot {
    width: 62px; height: 62px; border-radius: 50%;
    background: var(--brand-green); margin-right: 18px;
  }
  .back-lockup .brand-name { font-size: 48px; color: var(--brand-grey); }
  .back-lockup .tagline { font-size: 9px; color: var(--brand-grey); margin-top: 4px; letter-spacing: 2.2px; }
</style>
</head>
<body>

<section class="card card--front" aria-label="Card front">
  <div class="header-band">
    <div class="brand-name">Plavex</div>
    <div class="tagline">Technology Recruitment</div>
    <div class="header-accent"></div>
  </div>

  <div class="holder">
    <div class="holder-name"><span class="first">HARRIET</span> DUNMORE</div>
    <div class="holder-role">Managing Director</div>
  </div>

  <ul class="contacts">
    <li><svg viewBox="0 0 10 10"><path d="M1 4 Q5 0 9 4 L8 5 L6.5 4 L6.5 3 Q5 2.5 3.5 3 L3.5 4 L2 5 Z M2.5 5 H7.5 V9 H2.5 Z"/></svg>01632 960418</li>
    <li><svg viewBox="0 0 10 10"><path d="M3 0.5 H7 Q7.5 0.5 7.5 1 V9 Q7.5 9.5 7 9.5 H3 Q2.5 9.5 2.5 9 V1 Q2.5 0.5 3 0.5 Z M3.3 1.5 V7.5 H6.7 V1.5 Z"/></svg>01632 960418</li>
    <li><svg viewBox="0 0 10 10"><path d="M3 0.5 H7 V3 H9 V9.5 H1 V3 H3 Z M2.5 5 V6 H7.5 V5 Z M2.5 7 V8 H7.5 V7 Z"/></svg>01632 960418</li>
    <li><svg viewBox="0 0 10 10"><path d="M0.5 2 H9.5 V8.5 H0.5 Z M1.2 2.6 L5 5.6 L8.8 2.6 Z" fill-rule="evenodd"/></svg>Harriet@plavex.co.uk</li>
  </ul>

  <address class="address">
    Brackwell House, Partridge Way<br>
    Fenmoor Enterprise Park, QB9 3KX
  </address>
</section>

<section class="card card--back" aria-label="Card back">
  <div class="back-lockup">
    <div class="back-dot"></div>
    <div>
      <div class="brand-name">Plavex</div>
      <div class="tagline">Technology Recruitment</div>
    </div>
  </div>
</section>

</body>
</html>
```